FinTech company looking to revamp and expand client-facing interface for our financial models

Pellworth Engines currently has a very simple website that allows clients to interact with our financial models. We are looking to completely redesign the current site and add several extra pages to provide extra functionality. We want the design to have a modern, slick feel, that will work on both a desktop or a tablet. It should be straightforward for clients to move between different pages at any time, and clear from the layout how to interact with the more advanced features. We have included screenshots of existing pages in the attached design brief, as well as sketches of the functionality required by the new pages, but can't provide a direct link to the current site.
Target Market(s)
Professional investors that will be paying to access the interface
Industry/Entity Type
Finance
Number of Pages Required
4 page
Colors
Designer to choose colors to be used in the design.
Look and feel
Each slider illustrates characteristics of the customer's brand and the style your logo design should communicate.

```html
<!DOCTYPE html>
<html lang="en">
<head>
<meta charset="utf-8">
<title>QORVA – Models</title>
<link href="https://fonts.googleapis.com/css2?family=Montserrat:wght@500;600;700&family=Open+Sans:wght@400;700&family=Roboto+Condensed:wght@400&display=swap" rel="stylesheet">
<style>
:root{
  --frame:#e6e6e6;
  --page:#fafafa;
  --nav:#333333;
  --nav-active:#000000;
  --nav-text:#d0d0d0;
  --nav-divider:#444444;
  --accent:#3a8ee6;
  --head-top:#2b8ff0;
  --head-bottom:#0a3d7d;
  --cell-text:#111111;
  --grid:#d6d6d6;
  --row-alt:#f6f6f6;
  --input-border:#c9c9c9;
}
*{box-sizing:border-box;margin:0;padding:0}
html,body{width:1200px;height:655px;overflow:hidden;background:var(--frame)}
.app{position:absolute;left:14px;top:14px;width:1172px;height:627px;
  background:linear-gradient(160deg,#ffffff 0%,#f4f4f4 60%,#efefef 100%);}
.topbar{position:absolute;left:0;top:0;width:1172px;height:55px;background:var(--nav);
  font-family:"Montserrat",sans-serif;color:var(--nav-text)}
.brand{position:absolute;left:53px;top:0;line-height:55px;font-weight:700;font-size:16px;color:#fff}
.period-tabs{position:absolute;left:166px;top:0;display:flex;height:55px}
.period-tab{width:83px;height:55px;line-height:55px;text-align:center;font-size:12px;font-weight:600;
  border-right:1px solid var(--nav-divider)}
.period-tab.is-active{background:var(--nav-active);color:var(--accent)}
.main-nav{position:absolute;left:697px;top:0;display:flex;height:55px}
.main-nav-item{display:flex;align-items:center;justify-content:center;gap:7px;height:55px;
  font-size:12px;font-weight:600;border-right:1px solid var(--nav-divider)}
.main-nav-item svg{width:20px;height:20px}
.main-nav-item.models{width:129px;background:var(--nav-active);color:var(--accent)}
.main-nav-item.sensitivities{width:164px}
.main-nav-item.favourites{width:182px;border-right:none}
.dropdown{position:absolute;left:697px;top:55px;width:166px;height:116px;background:var(--nav-active);
  padding:15px 0 0 25px;font-family:"Montserrat",sans-serif;font-size:11.5px;font-weight:600;color:#cfcfcf;line-height:18px}
.filters{position:absolute;left:53px;top:92px;font-family:"Open Sans",sans-serif;font-size:15px;color:#111}
.filter-row{display:flex;align-items:center;height:36px}
.filter-name{width:78px}
.filter-label{width:93px;font-weight:700}
.filter-input{width:166px;height:28px;border:1px solid var(--input-border);border-radius:4px;background:#fff;
  padding-left:10px;line-height:26px;font-size:15px;box-shadow:inset 0 1px 2px rgba(0,0,0,.08)}
.export{position:absolute;left:1038px;top:146px;display:flex;align-items:center;gap:8px;
  font-family:"Montserrat",sans-serif;font-weight:600;font-size:15px;color:var(--accent)}
.export svg{width:23px;height:22px}
.models-table{position:absolute;left:51px;top:184px;width:1070px;border-collapse:separate;border-spacing:0;
  border-radius:6px;overflow:hidden;box-shadow:0 2px 8px rgba(0,0,0,.18);background:#fff;table-layout:fixed}
.models-table th{height:65px;background:linear-gradient(var(--head-top),var(--head-bottom));color:#fff;
  font-family:"Montserrat",sans-serif;font-weight:600;font-size:15px;border-right:1px solid rgba(0,0,0,.35)}
.models-table th:last-child,.models-table td:last-child{border-right:none}
.models-table td{height:64.6px;font-family:"Roboto Condensed","Arial Narrow",sans-serif;font-size:15.5px;
  color:var(--cell-text);border-right:1px solid var(--grid);border-top:1px solid var(--grid);padding-left:8px;line-height:19px}
.models-table td.model-id{text-align:center;padding-left:0}
.models-table td.time{text-align:center;padding-left:0}
.models-table tbody tr:nth-child(even) td{background:var(--row-alt)}
.sort-caret{font-size:10px;margin-left:4px}
</style>
</head>
<body>
<div class="app">
  <header class="topbar">
    <div class="brand">QORVA</div>
    <nav class="period-tabs">
      <div class="period-tab is-active">250D</div>
      <div class="period-tab">83D</div>
      <div class="period-tab">42D</div>
    </nav>
    <nav class="main-nav">
      <div class="main-nav-item models">
        <svg viewBox="0 0 24 24" fill="none" stroke="currentColor" stroke-width="2" stroke-linejoin="round"><path d="M3 11 12 3l9 8"/><path d="M5 10v10h5v-6h4v6h5V10"/></svg>MODELS</div>
      <div class="main-nav-item sensitivities">
        <svg viewBox="0 0 24 24" fill="none" stroke="currentColor" stroke-width="1.5"><circle cx="12" cy="12" r="4"/><circle cx="12" cy="12" r="8" stroke-dasharray="2 2"/></svg>SENSITIVITIES</div>
      <div class="main-nav-item favourites">
        <svg viewBox="0 0 24 24" fill="none" stroke="currentColor" stroke-width="1.6" stroke-linejoin="round"><path d="M12 2.5l2.9 6.2 6.6.7-5 4.5 1.4 6.6L12 17.2l-5.9 3.3 1.4-6.6-5-4.5 6.6-.7z"/></svg>FAVOURITES</div>
    </nav>
  </header>
  <div class="dropdown">
    <div>EQUITIES</div><div>ETFS</div><div>PAIRS</div><div>ETF PAIRS</div><div>FACTORS</div>
  </div>

  <section class="filters">
    <div class="filter-row"><span class="filter-name">Quality</span><span class="filter-label">Threshold:</span><div class="filter-input">-10</div></div>
    <div class="filter-row"><span class="filter-name"><b>Abs.</b> Stat</span><span class="filter-label">Threshold:</span><div class="filter-input">-10</div></div>
  </section>

  <div class="export">
    <svg viewBox="0 0 24 24" fill="none" stroke="currentColor" stroke-width="2" stroke-linecap="round" stroke-linejoin="round"><path d="M11 4H6a3 3 0 0 0-3 3v11a3 3 0 0 0 3 3h11a3 3 0 0 0 3-3v-5"/><path d="M9 15c1-5 5-8 11-8"/><path d="M16 3l4 4-4 4"/></svg>Export</div>

  <table class="models-table">
    <colgroup><col style="width:92px"><col style="width:102px"><col style="width:106px"><col style="width:106px"><col style="width:83px"><col style="width:83px"><col style="width:83px"><col style="width:83px"><col style="width:83px"><col style="width:83px"><col style="width:83px"><col style="width:83px"></colgroup>
    <thead><tr><th>ID<span class="sort-caret">&#9013;</span></th><th>Sector</th><th>Time</th><th>Quality</th><th>Stat 1</th><th>Stat 2</th><th>Stat 3</th><th>Stat 4</th><th>Stat 5</th><th>Stat 6</th><th>Stat 7</th><th>Stat 8</th></tr></thead>
    <tbody>
      <tr><td class="model-id">Model 1</td><td>Materials</td><td class="time">2019-07-03<br>12:15:00.000</td><td>30.2288</td><td>2.01574</td><td>23.305</td><td>-0.149368</td><td>22.3054</td><td>4.63714</td><td>0.945706</td><td>2.81949</td><td>2.60858</td></tr>
      <tr><td class="model-id">Model 2</td><td>Industrials</td><td class="time">2019-07-03<br>12:15:00.000</td><td>32.8694</td><td>0.87307</td><td>32.185</td><td>-0.033692</td><td>33.9911</td><td>11.5693</td><td>-0.472968</td><td>-0.830458</td><td>6.80646</td></tr>
      <tr><td class="model-id">Model 3</td><td>Consumer<br>Discretionary</td><td class="time">2019-07-03<br>12:15:00.000</td><td>1.66002</td><td>-0.569222</td><td>159.814</td><td>0.0252328</td><td>172.616</td><td>10.2875</td><td>-0.750396</td><td>-0.385309</td><td>4.69146</td></tr>
      <tr><td class="model-id">Model 4</td><td>Information<br>Technology</td><td class="time">2019-07-03<br>12:15:00.000</td><td>45.6856</td><td>0.412148</td><td>202.488</td><td>0.0084923</td><td>205.834</td><td>11.9094</td><td>-0.137913</td><td>0.449595</td><td>3.85106</td></tr>
      <tr><td class="model-id">Model 5</td><td>Information<br>Technology</td><td class="time">2019-07-03<br>12:15:00.000</td><td>75.7733</td><td>7.06728</td><td>188.605</td><td>0.016913</td><td>161.665</td><td>3.82241</td><td>0.981019</td><td>1.29847</td><td>3.34927</td></tr>
    </tbody>
  </table>
</div>
</body>
</html>
```